Marwick Law Letterhead

We need a new letterhead design for a Law Firm. The address for the law firm is 1475 Calloway Street, Suite 210, Houston, Texas 77041. Phone Number: 832-361-9027; Fax Number: 832-614-7359. The logo is uploaded to the project.

```html
<!DOCTYPE html>
<html lang="en">
<head>
<meta charset="utf-8">
<title>Marwick Law Letterhead</title>
<link rel="stylesheet" href="https://fonts.googleapis.com/css2?family=Tinos:wght@400&family=Raleway:wght@400;600;700&display=swap">
<style>
  :root {
    --backdrop: #ebe4d7;
    --paper: #ffffff;
    --navy: #1f2f66;
    --red: #c8232c;
    --ink: #2a2a2a;
    --muted: #444444;
    --footer-tone: #e3e5ee;
  }
  * { box-sizing: border-box; margin: 0; padding: 0; }
  html, body {
    width: 1200px; height: 1200px; overflow: hidden;
    background: var(--backdrop);
  }
  .letterhead {
    position: absolute; left: 167px; top: 40px;
    width: 866px; height: 1120px;
    background: var(--paper);
    overflow: hidden;
    box-shadow: 0 2px 10px rgba(0,0,0,0.12);
  }
  .masthead {
    position: absolute; top: 70px; left: 0; right: 0;
    text-align: center;
  }
  .brand { display: inline-flex; align-items: center; gap: 16px; }
  .brand-mark { width: 46px; height: 46px; background: var(--navy); }
  .brand-name {
    font-family: "Tinos", "Times New Roman", serif;
    font-weight: 400; font-size: 50px; color: var(--navy);
    letter-spacing: 1px;
  }
  .brand-rule {
    width: 250px; height: 1px; background: var(--red);
    margin: 10px auto 0;
  }
  .contact-line {
    margin-top: 26px;
    font-family: "Tinos", "Times New Roman", serif;
    font-size: 15px; color: var(--navy);
    display: flex; justify-content: center; gap: 22px;
  }
  .letter {
    position: absolute; left: 110px; top: 250px; width: 620px;
    font-family: "Raleway", Arial, sans-serif;
    color: var(--ink);
  }
  .recipient { font-size: 12px; font-weight: 700; line-height: 1.35; }
  .recipient-phone { font-size: 13px; font-weight: 400; color: var(--muted); }
  .salutation { margin-top: 34px; font-size: 12px; font-weight: 700; }
  .letter p.body {
    margin-top: 20px; font-size: 12.5px; line-height: 1.85;
    text-align: justify;
  }
  .sign-off { margin-top: 38px; font-size: 11.5px; line-height: 1.4; }
  .sign-off strong { font-weight: 700; }
  .signature {
    margin-top: 10px; width: 140px; height: 40px;
    background: #ececec;
    border-radius: 4px;
  }
  .footer-band {
    position: absolute; left: 0; right: 0; bottom: 0;
    height: 90px;
    background: var(--footer-tone);
  }
</style>
</head>
<body>
  <main class="letterhead">
    <header class="masthead">
      <div class="brand">
        <span class="brand-mark"></span>
        <span class="brand-name">Marwick Law</span>
      </div>
      <div class="brand-rule"></div>
      <div class="contact-line">
        <span>1475 Calloway Street, Suite 210, Houston, Texas 77041</span>
        <span>Tel: 832-361-9027</span>
        <span>Fax: 832-614-7359</span>
      </div>
    </header>

    <section class="letter">
      <div class="recipient">418 Harbor Crest Lane<br>Los Angeles, CA 90021</div>
      <div class="recipient-phone">714-390-5162</div>

      <div class="salutation">Dear Mr. Ortland</div>

      <p class="body">Fusce scelerisque sem sem, non interdum ligula gravida id. Curabitur sit amet molestie elit. Pellentesque ac congue diam. Duis varius suscipit elementum. Ut ac volutpat arcu, id commodo erat. Suspendisse tempor diam ut nunc egestas finibus. Maecenas quis porttitor dolor, a accumsan odio. Phasellus nisl metus, consectetur ut venenatis sit amet, imperdiet at nunc.</p>

      <p class="body">Donec facilisis malesuada ipsum sit amet vulputate. Integer justo justo, fermentum vitae pellentesque feugiat, ullamcorper non velit. Suspendisse molestie volutpat nisl at faucibus. Praesent posuere sodales libero, sed lacinia lacus ultrices eu. Phasellus lobortis, lectus sit amet vehicula hendrerit, risus purus blandit nunc, porttitor dictum arcu nisl varius ipsum. Nam tempus et purus sit amet cursus. Ut nec mauris quam. Integer condimentum quis magna id tempus. Pellentesque et orci scelerisque nisi faucibus egestas et at orci. Aliquam placerat ultricies erat id tincidunt. Nunc quis justo ipsum. Pellentesque at nisl et nulla posuere sollicitudin vitae vel ex. Vivamus fermentum orci sem. Phasellus tempor, metus vitae rutrum varius, ex libero mattis sapien, nec dictum enim augue non augue. Vestibulum in orci ut augue iaculis porttitor.</p>

      <p class="body">Praesent sit amet augue auctor, ultrices dui eget, pellentesque enim. Vivamus eu elementum odio. Nulla vitae enim porta, posuere tellus in, euismod nulla. Pellentesque vitae sodales ligula, vitae viverra nunc. Integer tristique sit amet leo vel feugiat.</p>

      <div class="sign-off">
        <strong>Daniel R. Keats</strong><br>
        Marketing Manager
        <div class="signature" role="img" aria-label="Handwritten signature"></div>
      </div>
    </section>

    <div class="footer-band" role="img" aria-label="Plain decorative footer area"></div>
  </main>
</body>
</html>
```